Business Card Design Project for Heron Lending

Hello there,

We are looking for a business card design for our new Heron Lending car financing company. We are looking for a business card that will include:

- An address
- Telephone number and extension
- Employee Name
- Employee Title
- Our logo and name clearly visible

We are including our logo with this writeup, we are looking to convey friendliness, trus and memorability. Colors and everything else is up to you.

Target Market(s)

18-34 year old males and females

Industry/Entity Type

Business

```html
<!DOCTYPE html>
<html lang="en">
<head>
<meta charset="utf-8">
<title>Heron Lending business cards</title>
<link rel="stylesheet" href="https://fonts.googleapis.com/css2?family=Arimo:wght@400;700&display=swap">
<style>
  :root {
    --bg: #d9dadd;
    --card: #ffffff;
    --navy: #0f2460;
    --navy-ink: #1c2f6e;
    --mark-faint: #e6e9ec;
    --on-navy: #ffffff;
    --shadow: rgba(20, 25, 40, 0.18);
  }
  * { box-sizing: border-box; margin: 0; padding: 0; }
  html, body {
    width: 1200px;
    height: 960px;
    overflow: hidden;
    background: var(--bg);
    font-family: "Arimo", Arial, sans-serif;
  }
  .sheet {
    position: relative;
    width: 1200px;
    height: 960px;
    display: flex;
    align-items: center;
    justify-content: center;
    gap: 60px;
  }
  .card {
    position: relative;
    width: 540px;
    height: 320px;
    background: var(--card);
    border-radius: 16px;
    overflow: hidden;
    box-shadow: 0 10px 26px var(--shadow);
  }
  .brand {
    position: absolute;
    display: flex;
    align-items: center;
    gap: 10px;
    color: var(--navy-ink);
    font-weight: 400;
    font-size: 26px;
    letter-spacing: 3px;
    text-transform: uppercase;
    white-space: nowrap;
  }
  .brand-dot {
    width: 16px;
    height: 16px;
    border-radius: 50%;
    background: var(--navy-ink);
  }
  .card-front .brand { top: 92px; right: 36px; }
  .front-decor {
    position: absolute;
    left: -70px;
    bottom: -90px;
    width: 300px;
    height: 300px;
    border-radius: 50%;
    background: var(--mark-faint);
  }
  .card-back .band {
    position: absolute;
    inset: 0;
    width: 540px;
    height: 320px;
  }
  .card-back .brand { top: 104px; right: 30px; font-size: 22px; letter-spacing: 2px; }
  .contact-block {
    position: absolute;
    left: 34px;
    top: 0;
    bottom: 0;
    color: var(--on-navy);
  }
  .employee-name {
    position: absolute;
    top: 150px;
    font-weight: 700;
    font-size: 22px;
    white-space: nowrap;
  }
  .employee-title {
    position: absolute;
    top: 178px;
    font-size: 15px;
    white-space: nowrap;
  }
  .contact-list {
    position: absolute;
    top: 232px;
    list-style: none;
    font-size: 14px;
    line-height: 19px;
    white-space: nowrap;
  }
  .contact-list li {
    display: flex;
    align-items: flex-start;
    gap: 10px;
  }
  .contact-list svg { width: 12px; height: 12px; margin-top: 3px; fill: var(--on-navy); flex: none; }
</style>
</head>
<body>
<main class="sheet">
  <section class="card card-front" aria-label="Card front">
    <div class="front-decor" aria-hidden="true"></div>
    <div class="brand"><span class="brand-dot"></span>Heron Lending</div>
  </section>

  <section class="card card-back" aria-label="Card back">
    <svg class="band" viewBox="0 0 540 320" aria-hidden="true">
      <path d="M0 0 H210 C245 120 300 240 330 320 H0 Z" fill="var(--navy)"/>
      <path d="M216 0 C251 120 306 240 336 320" fill="none" stroke="var(--navy)" stroke-width="1.5"/>
    </svg>
    <div class="brand"><span class="brand-dot"></span>Heron Lending</div>
    <div class="contact-block">
      <p class="employee-name">Employee Name</p>
      <p class="employee-title">Managing Director</p>
      <ul class="contact-list">
        <li>
          <svg viewBox="0 0 12 12"><circle cx="6" cy="3.5" r="3"/><path d="M0 12 C0 7.5 12 7.5 12 12 Z"/></svg>
          <span>0012 3456 789</span>
        </li>
        <li>
          <svg viewBox="0 0 12 12"><path d="M6 0 L12 6 H10 V12 H7 V8 H5 V12 H2 V6 H0 Z"/></svg>
          <span>Your Adress Inc 2nd Lane<br>Ave Maple Falls, NJ 00000</span>
        </li>
      </ul>
    </div>
  </section>
</main>
</body>
</html>
```